Wordpress Design Project (Nerith)

We need a wordpress design for an established auction and real estate company based in Pennsylvania. The winning design will incorporate a professional layout with and company logo in a very simple and clean layout.

Industry/Entity Type

Real Estate

Requirements
Must have
• Navigation:
1) Home; 2) Auctions; 3) Appraisals; 4) Real Estate; 5) FAQ; 6) About Us; 7) Contact Us.

Site will have overall layout of https://www.plumvarro.com/featured/regions/the-northeast. Home page will have logo and navigation at top. The navigation bar will also have social media icons (facebook, Google+, RSS, twitter) inside it. There will be text in the content area - use lorem ipsum. The image attached will be used below text (auctions.jpg) . Footer will have smaller company loogo, the attached affiliation logos and social media icons.

Logo attached. Color scheme will be black, gray, and red as accent color.
Nice to have
• navigation will have dropdowns, nice to have one represented - under auctions 'All Auctions' will be dropdown.

```html
<!DOCTYPE html>
<html lang="en">
<head>
<meta charset="utf-8">
<title>Nerith Auctioneers &amp; Appraisers</title>
<link href="https://fonts.googleapis.com/css2?family=Source+Sans+3:wght@300;400;600&display=swap" rel="stylesheet">
<style>
:root{
  --red:#d9262b;
  --red-dark:#b51d22;
  --ink:#333333;
  --text:#555555;
  --muted:#777777;
  --page:#f1f1f1;
  --card:#ffffff;
  --line:#e2e2e2;
  --footer-top:#e44a3c;
  --footer-bottom:#d8281f;
}
*{box-sizing:border-box;margin:0;padding:0}
html,body{width:984px;height:1200px;overflow:hidden}
body{position:relative;background:var(--page);font-family:"Source Sans 3",sans-serif;color:var(--ink)}
.abs{position:absolute}

/* header */
.site-header{left:0;top:0;width:984px;height:104px;background:#fff;border-bottom:1px solid #d4d4d4}
.brand{left:76px;top:29px;display:flex;align-items:center;gap:8px}
.brand-mark{width:54px;height:54px;background:var(--red);border-radius:3px}
.brand-name{font-size:34px;font-weight:600;color:var(--red);letter-spacing:1px;line-height:1}
.social{left:582px;top:18px;display:flex;gap:4px}
.social span{width:20px;height:20px;border-radius:3px;background:#8a8a8a}
.search{left:692px;top:14px;width:211px;height:27px;border:1px solid #cfcfcf;border-radius:3px;background:#fff;font-size:10px;font-style:italic;color:#999;padding:6px 9px}
.search svg{position:absolute;right:7px;top:6px}
.main-nav{right:79px;top:62px;display:flex;font-size:15px;color:var(--red)}
.main-nav a{color:inherit;text-decoration:none;padding:0 8px;border-left:1px solid #cccccc;line-height:16px}
.main-nav a:first-child{border-left:0}
.main-nav a:last-child{padding-right:0}

/* hero */
.hero{left:72px;top:117px;width:840px;height:294px;background:var(--card);border:1px solid #e8e8e8;border-radius:3px}
.hero h1{position:absolute;left:45px;top:45px;font-size:30px;font-weight:400;color:var(--red)}
.hero h2{position:absolute;left:45px;top:84px;font-size:23px;font-weight:400;color:#444}
.hero p{position:absolute;left:46px;top:118px;width:310px;font-size:11px;font-weight:300;line-height:19px;color:var(--text)}
.btn-find{position:absolute;left:47px;top:185px;width:98px;height:31px;background:linear-gradient(#d42a2f,#b81c21);color:#fff;font-size:12px;border-radius:3px;text-align:center;line-height:31px;box-shadow:0 1px 2px rgba(0,0,0,.3)}
.hero-arrows{position:absolute;left:47px;top:238px}
.hero-visual{position:absolute;left:453px;top:59px;width:361px;height:177px;background:linear-gradient(135deg,#d0d0d0,#9a9a9a);border-radius:40px 60px 30px 50px;opacity:.7}

/* listings */
.listing{width:410px;height:221px;background:var(--card);border:1px solid #e6e6e6;border-radius:3px}
.listing-photo{position:absolute;left:14px;top:11px;width:384px;height:152px;border-radius:2px}
.listing-title{position:absolute;left:20px;top:169px;font-size:16px;color:#444}
.listing-desc{position:absolute;left:20px;top:194px;font-size:10.5px;color:var(--text)}
.listing-loc{position:absolute;right:12px;top:170px;font-size:12px;color:var(--red);display:flex;align-items:center;gap:4px}
.photo-cabinets{background:linear-gradient(90deg,#c79a6e,#6b2a1f 45%,#8a4a35 80%,#b89a7c)}
.photo-vanities{background:linear-gradient(180deg,#c9a584,#3b3632 45%,#a3672f)}
.photo-carpet{background:linear-gradient(135deg,#b8ab8c,#8f8a86 50%,#6a6c74)}
.photo-doors{background:linear-gradient(90deg,#b5c4d6,#e8ecef 50%,#c08a55)}

/* subscribe + affiliations */
.extras{left:0;top:921px;width:984px;height:158px;background:#fff;border-top:1px solid #e3e3e3}
.extras h3{position:absolute;font-size:20px;font-weight:400;color:#333}
.subscribe-note{position:absolute;left:81px;top:64px;font-size:11.5px;font-weight:300;color:var(--muted)}
.email{position:absolute;left:80px;top:92px;width:250px;height:32px;background:#ececec;border-radius:3px 0 0 3px;font-size:12px;color:#999;padding:8px 14px}
.btn-sign{position:absolute;left:330px;top:92px;width:96px;height:32px;background:linear-gradient(#444,#2a2a2a);color:#fff;font-size:13px;border-radius:0 3px 3px 0;text-align:center;line-height:32px}
.badges{position:absolute;left:485px;top:68px;display:flex;gap:20px;align-items:center}
.badges span{width:52px;height:48px;background:#bdbdbd}
.badges .round{border-radius:50%;width:56px}

/* footer */
.site-footer{left:0;top:1079px;width:984px;height:121px;background:linear-gradient(var(--footer-top),var(--footer-bottom))}
.footer-nav{position:absolute;left:87px;top:29px;display:flex;font-size:14px;color:#fff}
.footer-nav a{color:inherit;text-decoration:none;padding:0 9px;border-left:1px solid #fff;line-height:14px}
.footer-nav a:first-child{border-left:0;padding-left:0}
.copyright{position:absolute;left:88px;top:60px;font-size:11px;color:#fde3e0}
.footer-brand{position:absolute;left:738px;top:26px;display:flex;align-items:center;gap:6px}
.footer-brand .brand-mark{width:46px;height:46px;background:rgba(255,255,255,.55)}
.footer-brand .brand-name{font-size:29px;color:rgba(255,255,255,.7)}
</style>
</head>
<body>

<header class="site-header abs">
  <div class="brand abs"><span class="brand-mark"></span><span class="brand-name">NERITH</span></div>
  <div class="social abs" aria-label="Social links"><span></span><span></span><span></span><span></span></div>
  <div class="search abs">Search here..
    <svg width="14" height="14" viewBox="0 0 14 14"><circle cx="6" cy="6" r="4.5" fill="none" stroke="#888" stroke-width="1.6"/><line x1="9.3" y1="9.3" x2="13" y2="13" stroke="#888" stroke-width="1.8"/></svg>
  </div>
  <nav class="main-nav abs">
    <a href="#">Home</a><a href="#">Auctions</a><a href="#">Appraisals</a><a href="#">Real Estate</a><a href="#">FAQ</a><a href="#">About Us</a><a href="#">Contact Us</a>
  </nav>
</header>

<section class="hero abs">
  <h1>Suspendisse vulputate aliquam</h1>
  <h2>Duis tincidunt lectus quis</h2>
  <p>Nunc tempus felis vitae urna. Vivamus porttitor, g, purus nisi eleifend libero, a tempus libero lectus feugiat felis. Morbi diam mauris, viverra in, gravida eu, mattis in, ante.</p>
  <div class="btn-find">FIND NOW</div>
  <svg class="hero-arrows" width="30" height="18" viewBox="0 0 30 18"><polyline points="10,1 2,9 10,17" fill="none" stroke="#444" stroke-width="1.6"/><polyline points="20,1 28,9 20,17" fill="none" stroke="#444" stroke-width="1.6"/></svg>
  <div class="hero-visual" role="img" aria-label="Striped grey world map"></div>
</section>

<article class="listing abs" style="left:72px;top:435px">
  <div class="listing-photo photo-cabinets" role="img" aria-label="Wooden cabinets with yellow auction tags"></div>
  <div class="listing-title">Tittle Name</div>
  <div class="listing-desc">The Home of Buffalo's Finest Finds</div>
  <div class="listing-loc"><svg width="12" height="16" viewBox="0 0 12 16"><path d="M6 0a6 6 0 0 0-6 6c0 4.5 6 10 6 10s6-5.5 6-10a6 6 0 0 0-6-6z" fill="#d9262b"/><circle cx="6" cy="6" r="2.3" fill="#fff"/></svg>New York , NY</div>
</article>
<article class="listing abs" style="left:501px;top:435px">
  <div class="listing-photo photo-vanities" role="img" aria-label="Bathroom vanities with granite tops"></div>
  <div class="listing-title">Tittle Name</div>
  <div class="listing-desc">The Home of Buffalo's Finest Finds</div>
  <div class="listing-loc"><svg width="12" height="16" viewBox="0 0 12 16"><path d="M6 0a6 6 0 0 0-6 6c0 4.5 6 10 6 10s6-5.5 6-10a6 6 0 0 0-6-6z" fill="#d9262b"/><circle cx="6" cy="6" r="2.3" fill="#fff"/></svg>Buffalo, NY</div>
</article>
<article class="listing abs" style="left:72px;top:671px">
  <div class="listing-photo photo-carpet" role="img" aria-label="Rolled carpets with yellow auction tags"></div>
  <div class="listing-title">Tittle Name</div>
  <div class="listing-desc">The Home of Buffalo's Finest Finds</div>
  <div class="listing-loc"><svg width="12" height="16" viewBox="0 0 12 16"><path d="M6 0a6 6 0 0 0-6 6c0 4.5 6 10 6 10s6-5.5 6-10a6 6 0 0 0-6-6z" fill="#d9262b"/><circle cx="6" cy="6" r="2.3" fill="#fff"/></svg>Buffalo, NY</div>
</article>
<article class="listing abs" style="left:501px;top:671px">
  <div class="listing-photo photo-doors" role="img" aria-label="Row of white and wooden doors"></div>
  <div class="listing-title">Tittle Name</div>
  <div class="listing-desc">The Home of Buffalo's Finest Finds</div>
  <div class="listing-loc"><svg width="12" height="16" viewBox="0 0 12 16"><path d="M6 0a6 6 0 0 0-6 6c0 4.5 6 10 6 10s6-5.5 6-10a6 6 0 0 0-6-6z" fill="#d9262b"/><circle cx="6" cy="6" r="2.3" fill="#fff"/></svg>Buffalo, NY</div>
</article>

<section class="extras abs">
  <h3 style="left:81px;top:33px">I want more stuff like this!</h3>
  <div class="subscribe-note">Subscribe and never miss out on finds &amp; deals delivered to your inbox.</div>
  <div class="email">email address</div>
  <div class="btn-sign">Sign Me Up</div>
  <h3 style="left:485px;top:34px">Affiliations</h3>
  <div class="badges" aria-label="Affiliation badges">
    <span></span><span class="round"></span><span class="round"></span><span></span><span></span><span class="round"></span>
  </div>
</section>

<footer class="site-footer abs">
  <nav class="footer-nav">
    <a href="#">Home</a><a href="#">Auctions</a><a href="#">Appraisals</a><a href="#">Real Estate</a><a href="#">FAQ</a><a href="#">About Us</a><a href="#">Contact Us</a>
  </nav>
  <div class="copyright">© 2013 Company Name.&nbsp; All right reserved.&nbsp; Term of Use</div>
  <div class="footer-brand"><span class="brand-mark"></span><span class="brand-name">NERITH</span></div>
</footer>

</body>
</html>
```